Sales Page Header Design Project

Hi,
I need a background image created for this sales page: http://trimventurecamp.com
Width: 977 px
Height: 150 px
Here are a few sample designs to work with: http://firmsummitschool.com/
http://craftingamarkweb.com/wp-content/uploads/2011/02/experts1.png
Must be sharp, professional looking and uncluttered.
Colours: Must include blue (I like the blue on the on the current sales page, but will leave shade and colour combinations to your creativity)
Text = Tobi Wanrenu Presents
Trim Venture Camp
Your Blueprint for Building a Profitable, Sustainable Business in Today's Economy!
Any questions, give me a shout
Entrepreneurs and Business Owners, aged 21 to 45
Business

```html
<!DOCTYPE html>
<html lang="en">
<head>
<meta charset="utf-8">
<title>Trim Venture Camp – Sales Page Header</title>
<link rel="stylesheet" href="https://fonts.googleapis.com/css2?family=Arimo:ital,wght@0,400;0,700;1,400&display=swap">
<style>
  :root {
    --page-bg: #f4f4f4;
    --banner-edge: #0a2234;
    --banner-mid: #1d5f92;
    --banner-center: #2f82c2;
    --text-white: #ffffff;
    --tagline-cyan: #22d3f0;
    --icon-grey: #4a4d52;
    --icon-blue: #2a9be0;
  }
  html, body {
    margin: 0;
    width: 1200px;
    height: 1000px;
    overflow: hidden;
    background: var(--page-bg);
    font-family: "Arimo", Arial, sans-serif;
  }
  .header-banner {
    position: absolute;
    left: 112px;
    top: 425px;
    width: 977px;
    height: 150px;
    background: radial-gradient(ellipse 60% 140% at 50% 40%, var(--banner-center) 0%, var(--banner-mid) 50%, var(--banner-edge) 100%);
    color: var(--text-white);
    text-align: center;
  }
  .presenter {
    position: absolute;
    top: 16px;
    left: 0;
    right: 0;
    font-size: 16px;
    letter-spacing: 0.2px;
  }
  .presenter small {
    font-size: 9px;
    letter-spacing: 1.5px;
    margin-left: 2px;
  }
  .title {
    position: absolute;
    top: 48px;
    left: 0;
    right: 0;
    display: flex;
    justify-content: center;
    align-items: flex-end;
    gap: 8px;
    height: 56px;
    font-size: 52px;
    line-height: 1;
    text-shadow: 0 2px 3px rgba(0,0,0,0.45);
  }
  .title-light { font-weight: 400; }
  .title-bold { font-weight: 700; letter-spacing: 1px; }
  .growth-icon { width: 62px; height: 56px; margin: 0 2px 2px; }
  .tagline {
    position: absolute;
    top: 117px;
    left: 0;
    right: 0;
    font-size: 16px;
    font-style: italic;
    letter-spacing: 0.4px;
    color: var(--tagline-cyan);
    text-shadow: 0 1px 2px rgba(0,0,0,0.5);
  }
</style>
</head>
<body>
  <header class="header-banner">
    <div class="presenter">Tobi Wanrenu <small>Presents</small></div>
    <h1 class="title" style="margin:0">
      <span class="title-light">Trim Venture</span>
      <svg class="growth-icon" viewBox="0 0 62 56" role="img" aria-label="Icon of a business person beside rising bars and an upward arrow">
        <defs>
          <linearGradient id="icon-fill" x1="0" y1="0" x2="1" y2="0">
            <stop offset="0" stop-color="var(--icon-grey)"/>
            <stop offset="1" stop-color="var(--icon-blue)"/>
          </linearGradient>
        </defs>
        <rect x="0" y="0" width="62" height="56" rx="3" fill="url(#icon-fill)"/>
      </svg>
      <span class="title-bold">Camp</span>
    </h1>
    <p class="tagline" style="margin:0">Your Blueprint for Building a Profitable, Sustainable Business in Today's Economy!</p>
  </header>
</body>
</html>
```